Design a "healthy, happy dog and cat" cheque/check background

I am looking for a few design concepts featuring a happy healthy dog and cat, that will be used as the background of a paper cheque/check.

This will require Photoshop and stock photos.

Here is the design brief: https://docs.plinvaro.com/document/d/4Rt8mKx2LqW9zVbN3cHy7TfJ1sDp6GaE0uYoZiXeMwnB/edit?usp=sharing

Colors

Designer to choose colors to be used in the design.

Requirements
Must have
• A happy dog and cat the main focus within the "empty" central part of the cheque/check, and a complementary background for the rest of the cheque, following the design guidelines in the attached plinvaro doc.

```html
<!DOCTYPE html>
<html lang="en">
<head>
<meta charset="utf-8">
<title>Personal Cheque – Dog Background</title>
<link rel="stylesheet" href="https://fonts.googleapis.com/css2?family=Arimo:wght@400;700&family=Share+Tech+Mono&display=swap">
<style>
  :root {
    --page: #ffffff;
    --ink: #1d1d1d;
    --ink-soft: #3a3a3a;
    --line: #2a2a2a;
    --fur-light: #e9dccb;
    --fur-mid: #c9a27a;
    --fur-dark: #6e5140;
    --wash: #f4f2ee;
    --field: #ffffff;
    --slogan: #ffffff;
    --frame-green: #9cc79a;
  }
  html, body {
    margin: 0;
    padding: 0;
    width: 1200px;
    height: 528px;
    overflow: hidden;
    background: var(--page);
  }
  .canvas {
    position: relative;
    width: 1200px;
    height: 528px;
    font-family: "Arimo", Arial, sans-serif;
    color: var(--ink);
  }
  .cheque {
    position: absolute;
    left: 18px;
    top: 14px;
    width: 1162px;
    height: 386px;
    overflow: hidden;
    background: var(--wash);
    border-right: 2px solid var(--frame-green);
  }
  .cheque__photo {
    position: absolute;
    inset: 0;
    width: 100%;
    height: 100%;
  }
  .abs { position: absolute; margin: 0; }

  .issuer__name { left: 34px; top: 42px; font-size: 22px; font-weight: 700; color: var(--ink-soft); }
  .issuer__line { left: 34px; font-size: 20px; color: var(--ink-soft); }
  .issuer__line--1 { top: 66px; }
  .issuer__line--2 { top: 88px; }

  .cheque__number { left: 994px; top: 36px; font-size: 26px; font-weight: 700; color: #000; }

  .date__label { left: 756px; top: 92px; font-size: 20px; color: var(--ink); }
  .date__boxes { left: 820px; top: 72px; display: flex; gap: 2px; }
  .date__box { width: 36px; height: 36px; background: var(--field); opacity: 0.85; }
  .date__keys { left: 820px; top: 112px; display: flex; gap: 2px; }
  .date__key { width: 36px; text-align: center; font-size: 13px; color: var(--ink); }

  .payee__label { left: 32px; top: 176px; font-size: 14px; line-height: 14px; text-transform: uppercase; color: var(--ink); }
  .amount__sign { left: 918px; top: 178px; font-size: 28px; color: var(--ink); }
  .amount__box { left: 944px; top: 156px; width: 210px; height: 46px; background: var(--field); }
  .amount__words { left: 890px; top: 232px; font-size: 16px; color: var(--ink); }

  .rules { position: absolute; inset: 0; width: 100%; height: 100%; pointer-events: none; }

  .bank__mark { left: 36px; top: 272px; width: 70px; height: 70px; border-radius: 50%; background: #1d1d1d; }
  .bank__name { left: 128px; top: 282px; font-size: 19px; font-weight: 700; }
  .bank__line { left: 128px; font-size: 18px; }
  .bank__line--1 { top: 304px; }
  .bank__line--2 { top: 322px; }

  .slogan { left: 720px; width: 350px; text-align: center; font-size: 15px; font-weight: 700; color: var(--slogan); }
  .slogan--en { top: 280px; }
  .slogan--fr { top: 299px; }
  .company { left: 720px; top: 319px; width: 350px; text-align: center; font-size: 14px; color: #000; }

  .memo__label { left: 38px; top: 368px; font-size: 12px; text-transform: uppercase; }

  .security { left: 1132px; top: 252px; width: 26px; height: 132px; border: 1px solid #555; background: #fff; }
  .security__text {
    position: absolute; left: 1px; top: 4px; width: 22px; height: 72px;
    writing-mode: vertical-rl; transform: rotate(180deg);
    font-size: 7px; line-height: 9px; text-align: center; color: #222;
  }
  .security__badge { position: absolute; left: 5px; bottom: 4px; width: 14px; height: 12px; background: #222; }

  .micr {
    left: 48px; top: 446px;
    font-family: "Share Tech Mono", "Courier New", monospace;
    font-size: 30px; letter-spacing: 4px; color: #111;
    word-spacing: 14px;
  }
</style>
</head>
<body>
<main class="canvas">
  <section class="cheque">
    <svg class="cheque__photo" viewBox="0 0 1162 386" preserveAspectRatio="none" role="img" aria-label="Faded close-up photo of a brown and tan dog's face filling the cheque background">
      <defs>
        <radialGradient id="furGlow" cx="0.5" cy="0.55" r="0.6">
          <stop offset="0" stop-color="var(--fur-mid)" stop-opacity="0.85"/>
          <stop offset="0.6" stop-color="var(--fur-light)" stop-opacity="0.8"/>
          <stop offset="1" stop-color="var(--wash)" stop-opacity="1"/>
        </radialGradient>
        <radialGradient id="furShade" cx="0.5" cy="0.35" r="0.35">
          <stop offset="0" stop-color="var(--fur-dark)" stop-opacity="0.35"/>
          <stop offset="1" stop-color="var(--fur-dark)" stop-opacity="0"/>
        </radialGradient>
      </defs>
      <rect width="1162" height="386" fill="var(--wash)"/>
      <rect width="1162" height="386" fill="url(#furGlow)"/>
      <rect width="1162" height="386" fill="url(#furShade)"/>
    </svg>

    <h1 class="abs issuer__name">Northvale Cheques Personal Cheque</h1>
    <p class="abs issuer__line issuer__line--1">15 Linden Grove Street</p>
    <p class="abs issuer__line issuer__line--2">Brookhaven, Ontario K9K 9K9</p>

    <p class="abs cheque__number">101</p>

    <p class="abs date__label">DATE</p>
    <div class="abs date__boxes">
      <span class="date__box"></span><span class="date__box"></span><span class="date__box"></span><span class="date__box"></span>
      <span class="date__box"></span><span class="date__box"></span><span class="date__box"></span><span class="date__box"></span>
    </div>
    <div class="abs date__keys">
      <span class="date__key">D</span><span class="date__key">D</span><span class="date__key">M</span><span class="date__key">M</span>
      <span class="date__key">Y</span><span class="date__key">Y</span><span class="date__key">Y</span><span class="date__key">Y</span>
    </div>

    <p class="abs payee__label">Pay to the<br>order of</p>
    <p class="abs amount__sign">$</p>
    <div class="abs amount__box"></div>
    <p class="abs amount__words">100 DOLLARS</p>

    <svg class="rules" viewBox="0 0 1162 386" aria-hidden="true">
      <g stroke="var(--line)" stroke-width="1.4" fill="none">
        <line x1="32" y1="202" x2="894" y2="202"/>
        <line x1="894" y1="174" x2="894" y2="202"/>
        <line x1="34" y1="256" x2="874" y2="256"/>
        <line x1="874" y1="256" x2="886" y2="220"/>
        <line x1="38" y1="378" x2="560" y2="378"/>
        <line x1="658" y1="378" x2="1070" y2="378"/>
      </g>
    </svg>

    <span class="abs bank__mark" aria-hidden="true"></span>
    <p class="abs bank__name">Your Financial Institution</p>
    <p class="abs bank__line bank__line--1">200 Finance Avenue</p>
    <p class="abs bank__line bank__line--2">Your City, Your Province A1B 2CS</p>

    <p class="abs slogan slogan--en">Help your local Pet Rescue League</p>
    <p class="abs slogan slogan--fr">Aidez votre Pet Rescue League locale</p>
    <p class="abs company">Optional Company Name</p>

    <p class="abs memo__label">Memo</p>

    <div class="abs security">
      <span class="security__text">Details on Back<br>Détails au Verso</span>
      <span class="security__badge" aria-hidden="true"></span>
    </div>
  </section>

  <p class="abs micr">⑈101⑈ ⑆12345⑉678⑆ 12345⑉6789⑈</p>
</main>
</body>
</html>
```